wardrobe/costume stylist needs good business card for own business

Hi:)

I'm wanting a business card for my company. I am a freelance stylist.

I do wardrobe/costume stylist to TV commercials; Films; Fashion and Lifestyle shoots.

I'd like a design based around my name Rosalind Parfrey written nicely, maybe a colour? Up to you?!

I've attached a couple of images of business cards I like
.... be creative and have fun!

Thank you :)

Reason: I was trying to get my new business card ready for before I headed overseas Friday morning but I don't think that was realistic so I'd like to extend the deadline to give time to the project. Thank you

Hi designers:) Thank you for all your designs, I've extended the deadline until Sunday, so there's a bit more time. I've attached 3 pictures of business cards which I quite like, please take a look to see if it can be of help in your process. I like the pale plain or patterned background with dark font and the dark plain or patterned background with the pale font the motifs the feminine fonts the plain fonts I like the idea of playing with a circle or some shape on one side of the card with my name or initials as in the picture I have on my post could you play around with this idea a bit please? Thank you all for the work you've done :) Rosa

Hi I am working overseas til Saturday night sorry for no feedback until I teturn Thanks :) Rosa

Hi designers, Thank you all so much for submitting your designs, I really appreciate your input into my project :) I'm sorry I didn't get to respond to some comments, and give feedback. I didn't back from being away until later than I expected, and the deadline had passed then, so apologies. Thanks to you all again for all your really good designs :) Rosa

Target Market(s)

I am a freelance stylist my target audience is producers, production companies, photographers, directors...

Industry/Entity Type

Business

Requirements
Must have
• Rosalind Parfrey
Stylist or Wardrobe Stylist

email rosaparfrey@mailbox-example.co.nz
Mobile 0218467193

(Don't have to use the words 'email' and 'mobile')
Nice to have
• Would like it to be double sided
Like B & W
Like pale colour background with dark font or white font
Like dark colour background with pale font
Should not have
• I would prefer it not to incorporate pictures

```html
<!DOCTYPE html>
<html lang="en">
<head>
<meta charset="utf-8">
<title>Rosalind Parfrey — Wardrobe Stylist</title>
<link rel="stylesheet" href="https://fonts.googleapis.com/css2?family=Pirata+One&family=Oswald:wght@300;500;600&family=Didact+Gothic&display=swap">
<style>
  :root {
    --paper: #eeeeed;
    --paper-shade: #e4e4e2;
    --ink-red: #9b1d20;
    --ink-red-soft: rgba(155, 29, 32, 0.55);
  }
  html, body {
    margin: 0;
    padding: 0;
    overflow: hidden;
    background: var(--paper);
  }
  .card {
    position: relative;
    width: 1200px;
    height: 702px;
    overflow: hidden;
    background: radial-gradient(ellipse at 40% 45%, var(--paper) 0%, var(--paper-shade) 100%);
    color: var(--ink-red);
  }
  .identity {
    position: absolute;
    left: 116px;
    top: 178px;
  }
  .identity__name {
    margin: 0;
    font-family: "Pirata One", fantasy;
    font-weight: 400;
    font-size: 66px;
    line-height: 1;
    letter-spacing: 1px;
  }
  .identity__role {
    margin: 6px 0 0 6px;
    font-family: "Oswald", sans-serif;
    font-weight: 300;
    font-size: 28px;
    line-height: 1;
    letter-spacing: 0.5px;
  }
  .contact {
    position: absolute;
    left: 116px;
    top: 346px;
    margin: 0;
    padding: 0;
    list-style: none;
  }
  .contact__row {
    display: flex;
    align-items: center;
    height: 76px;
  }
  .contact__label {
    width: 98px;
    font-family: "Oswald", sans-serif;
    font-weight: 600;
    font-size: 50px;
    line-height: 1;
  }
  .contact__phone {
    font-family: "Oswald", sans-serif;
    font-weight: 300;
    font-size: 42px;
    letter-spacing: 1px;
  }
  .contact__email {
    font-family: "Didact Gothic", sans-serif;
    font-size: 32px;
  }
  .flourish {
    position: absolute;
    left: 780px;
    top: 0;
    width: 420px;
    height: 610px;
  }
</style>
</head>
<body>
  <main class="card">
    <div class="identity">
      <h1 class="identity__name">Rosalind Parfrey</h1>
      <p class="identity__role">WARDROBE STYLIST</p>
    </div>

    <ul class="contact">
      <li class="contact__row">
        <span class="contact__label">M</span>
        <span class="contact__phone">0218467193</span>
      </li>
      <li class="contact__row">
        <span class="contact__label">E</span>
        <span class="contact__email">rosaparfrey@mailbox-example.co.nz</span>
      </li>
    </ul>

    <svg class="flourish" role="img" aria-label="Red swirling floral flourish ornament with curling tendrils and teardrop petals" viewBox="0 0 420 610">
      <defs>
        <radialGradient id="flourish-tone" cx="0.55" cy="0.38" r="0.62">
          <stop offset="0" stop-color="#9b1d20" stop-opacity="0.5"/>
          <stop offset="0.6" stop-color="#9b1d20" stop-opacity="0.22"/>
          <stop offset="1" stop-color="#9b1d20" stop-opacity="0"/>
        </radialGradient>
      </defs>
      <rect width="420" height="610" fill="url(#flourish-tone)"/>
    </svg>
  </main>
</body>
</html>
```